Black Car Limousine transportation business in Naples Florida

Always stand for my reliability and RVD stands for Love, K and M are the first initials of my children's names. It should show professionalism and a dedication to customer service. We keep our clients identities private. Show our professionalism. We are Black car Black tie company. We service transportation on a reserve basis to and from residents, airports, casinos, hotels,

Target Market(s)

It is a Private car service. High end clients. Businesses, Celebrity and athletes. Service to airports, hotels, special events.

Industry/Entity Type

Business

Contact Information for Business Card

A pearl metallic or Luster card. Standard business card size. Would like the name, Company email, show we take credit cards and phone number. Currently I don't have a website but will like to add later.

Logo Text

STEADFAST RVD TRANSPORTATION

Font styles to use
Serif

Colors
eaeaea
000000

Requirements
Must have
• Must have Company email, show we take credit cards and phone number. Currently I don't have a website but will like to add later.
Nice to have
• Would like to stay with a black and white theme. Open to some color trim.
Should not have
• Open to suggestions

```html
<!DOCTYPE html>
<html lang="en">
<head>
<meta charset="utf-8">
<title>Steadfast RVD Transportation – Business Card</title>
<link rel="stylesheet" href="https://fonts.googleapis.com/css2?family=Lora:ital,wght@0,400;0,600;0,700;1,700&display=swap">
<style>
  :root {
    --backdrop: #b7b7b7;
    --card: #ffffff;
    --ink: #111111;
    --ink-soft: #444444;
    --logo-grey: #8a8a8a;
    --photo-dark: #1b1b1b;
    --photo-mid: #4a4a4a;
    --shadow: rgba(0, 0, 0, 0.35);
  }
  * { box-sizing: border-box; margin: 0; padding: 0; }
  html, body {
    width: 1105px;
    height: 1200px;
    overflow: hidden;
    background: var(--backdrop);
    font-family: "Lora", Georgia, serif;
    color: var(--ink);
  }
  .card {
    position: absolute;
    left: 193px;
    width: 720px;
    height: 410px;
    background: var(--card);
    box-shadow: 2px 4px 6px var(--shadow);
  }
  .card--front { top: 167px; }
  .card--back { top: 623px; }

  .vehicle-photo {
    position: absolute;
    border-radius: 10px 18px 8px 8px;
    background: linear-gradient(180deg, var(--photo-mid) 0%, var(--photo-dark) 55%, #000 100%);
  }
  .card--front .vehicle-photo { left: 169px; top: 127px; width: 153px; height: 64px; }
  .card--back .vehicle-photo { left: 152px; top: 130px; width: 387px; height: 156px; border-radius: 30px 50px 20px 20px; }

  .logo-name {
    position: absolute;
    left: 334px;
    top: 124px;
    width: 230px;
    font-weight: 700;
    color: var(--logo-grey);
    line-height: 1;
    text-transform: uppercase;
    white-space: nowrap;
  }
  .logo-name__main { display: block; font-size: 27px; letter-spacing: 0.3px; }
  .logo-name__sub { display: block; font-size: 13px; letter-spacing: 4.6px; margin-top: 10px; }

  .holder {
    position: absolute;
    top: 286px;
    left: 0;
    width: 100%;
    text-align: center;
    white-space: nowrap;
  }
  .holder__name { font-size: 24px; font-weight: 600; color: var(--ink); }
  .holder__dash { font-size: 24px; font-weight: 600; margin: 0 10px 0 8px; }
  .holder__role { font-size: 18px; color: var(--ink-soft); }

  .contacts {
    position: absolute;
    top: 328px;
    left: 0;
    width: 100%;
    display: flex;
    justify-content: center;
    gap: 12px;
    font-size: 18px;
    color: var(--ink-soft);
    white-space: nowrap;
  }
  .contacts__item { display: flex; align-items: center; gap: 5px; }
  .contacts__icon { width: 18px; height: 18px; fill: var(--ink); }

  .payment-note {
    position: absolute;
    top: 335px;
    left: 0;
    width: 100%;
    display: flex;
    justify-content: center;
    align-items: center;
    gap: 8px;
    font-size: 19px;
    font-weight: 700;
    font-style: italic;
    color: var(--ink);
  }
  .payment-note__icon { width: 30px; height: 20px; }
</style>
</head>
<body>

<section class="card card--front" aria-label="Business card front">
  <div class="vehicle-photo" role="img" aria-label="Photo of a black luxury SUV"></div>
  <div class="logo-name">
    <span class="logo-name__main">Steadfast RVD</span>
    <span class="logo-name__sub">Transportation</span>
  </div>

  <p class="holder">
    <span class="holder__name">JOHN SMITH</span><span class="holder__dash">-</span><span class="holder__role">CEO/Founder</span>
  </p>

  <div class="contacts">
    <span class="contacts__item">
      <svg class="contacts__icon" viewBox="0 0 24 24" aria-hidden="true"><path d="M6.6 10.8a15.1 15.1 0 0 0 6.6 6.6l2.2-2.2a1 1 0 0 1 1-.25 11.4 11.4 0 0 0 3.6.57 1 1 0 0 1 1 1V20a1 1 0 0 1-1 1A17 17 0 0 1 3 4a1 1 0 0 1 1-1h3.5a1 1 0 0 1 1 1c0 1.25.2 2.45.57 3.57a1 1 0 0 1-.25 1z"/></svg>
      239 555 0173
    </span>
    <span class="contacts__item">
      <svg class="contacts__icon" viewBox="0 0 24 24" aria-hidden="true"><path d="M2 5h20v14H2z" fill="var(--ink)"/><path d="M3 6l9 7 9-7" fill="none" stroke="#fff" stroke-width="1.6"/></svg>
      ride@rvdcars.com
    </span>
    <span class="contacts__item">
      <svg class="contacts__icon" viewBox="0 0 24 24" aria-hidden="true"><circle cx="12" cy="12" r="10"/><path d="M7 8c2 0 3 1 3 2.5S8 13 9 15s1 4 0 5M14 4c0 2 2 2 3 3s-1 3 1 4 3 0 4 1" fill="none" stroke="#fff" stroke-width="1.6"/></svg>
      www.rvdcars.com
    </span>
  </div>
</section>

<section class="card card--back" aria-label="Business card back">
  <div class="vehicle-photo" role="img" aria-label="Photo of a black luxury SUV in side view"></div>
  <p class="payment-note">
    <svg class="payment-note__icon" viewBox="0 0 30 20" aria-hidden="true">
      <rect x="1" y="1" width="28" height="18" rx="3" fill="var(--ink)"/>
      <rect x="1" y="5" width="28" height="3" fill="#fff"/>
      <rect x="14" y="11" width="11" height="4" rx="1" fill="#fff"/>
    </svg>
    We accept credit cards
  </p>
</section>

</body>
</html>
```